Agriculture Business Card

I want to use my existing logo and use my tagline of "Don't Guess...Soil Test" on the card. Looking for a double sided card that will really get peoples attention.
Contact Info:
Marlow Field Crop Edge
Calvin Brusk
2917 K Lane
Larkin, NE 68593
402-555-0193
calvin.r.brusk@fieldmailbox.net

```html
<!DOCTYPE html>
<html lang="en">
<head>
<meta charset="utf-8">
<title>Marlow Field Crop Edge – Business Card</title>
<link rel="stylesheet" href="https://fonts.googleapis.com/css2?family=Oswald:wght@400&family=Roboto:wght@400;700&display=swap">
<style>
  :root {
    --stage: #7a7a7a;
    --soil: #985c3f;
    --leaf: #6cbf45;
    --paper: #ffffff;
    --bark: #8a4f35;
    --copper: #d29572;
    --ink-light: #ffffff;
  }
  * { box-sizing: border-box; margin: 0; padding: 0; }
  html, body {
    width: 1133px; height: 1200px; overflow: hidden;
    background: var(--stage);
  }
  .card {
    position: absolute;
    left: 205px;
    width: 722px; height: 412px;
    overflow: hidden;
  }
  .card-front { top: 150px; background: var(--paper); }
  .card-back  { top: 660px; background: var(--soil); }

  .front-band { position: absolute; inset: 0; }

  .contact {
    position: absolute; left: 42px; top: 122px;
    font-family: "Oswald", sans-serif;
    color: var(--ink-light);
  }
  .contact-name {
    font-size: 25px; font-weight: 400; color: var(--leaf);
    letter-spacing: 0.2px; text-transform: uppercase;
    margin-bottom: 14px;
  }
  .contact-address { font-size: 17px; line-height: 21px; margin-bottom: 12px; }
  .contact-lines { list-style: none; font-size: 17px; line-height: 21px; }
  .contact-lines li { display: flex; align-items: center; gap: 9px; }
  .contact-lines svg { width: 13px; height: 13px; flex: none; }

  .front-brand {
    position: absolute; left: 400px; top: 0; width: 290px; height: 412px;
    display: flex; flex-direction: column; justify-content: center; align-items: center;
    font-family: "Oswald", sans-serif; font-weight: 400;
    color: var(--bark); font-size: 30px; line-height: 36px; text-align: center;
  }

  .back-brand {
    position: absolute; left: 0; right: 0; top: 120px;
    text-align: center;
    font-family: "Oswald", sans-serif; font-weight: 400;
    font-size: 40px; line-height: 48px; color: var(--copper);
  }
  .tagline {
    position: absolute; left: 0; right: 0; top: 346px;
    text-align: center;
    font-family: "Roboto", sans-serif; font-size: 16px;
    letter-spacing: 2.4px; color: var(--ink-light);
  }
  .tagline strong { font-weight: 700; }
</style>
</head>
<body>

<section class="card card-front">
  <svg class="front-band" viewBox="0 0 722 412" aria-hidden="true">
    <path d="M0 0 H244 C312 10 300 150 310 250 C320 360 340 400 378 412 H0 Z" fill="var(--leaf)"/>
    <path d="M0 0 H234 C300 10 290 150 300 250 C310 360 330 400 366 412 H0 Z" fill="var(--soil)"/>
  </svg>

  <div class="contact">
    <h1 class="contact-name">Calvin Brusk</h1>
    <p class="contact-address">2917 K Lane<br>Larkin, NE 68593</p>
    <ul class="contact-lines">
      <li>
        <svg viewBox="0 0 16 16"><path d="M4 1 L6.5 4.5 L5 6.5 C6 8.5 7.5 10 9.5 11 L11.5 9.5 L15 12 L13 15 C7 15 1 9 1 3 Z" fill="var(--leaf)"/></svg>
        402-555-0193
      </li>
      <li>
        <svg viewBox="0 0 16 16"><rect x="1" y="3" width="14" height="10" fill="var(--leaf)"/><path d="M1 3 L8 9 L15 3" fill="none" stroke="var(--soil)" stroke-width="1.4"/></svg>
        calvin.r.brusk@fieldmailbox.net
      </li>
      <li>
        <svg viewBox="0 0 16 16"><circle cx="8" cy="8" r="7" fill="var(--leaf)"/><path d="M5 4 C7 5 6 7 8 8 C10 9 9 11 7 13 M10 3 C11 5 13 5 14 7" fill="none" stroke="var(--soil)" stroke-width="1.3"/></svg>
        marlowcropedge.com
      </li>
    </ul>
  </div>

  <div class="front-brand">
    <span>Marlow Field</span>
    <span>Crop Edge</span>
  </div>
</section>

<section class="card card-back">
  <div class="back-brand">Marlow Field<br>Crop Edge</div>
  <p class="tagline">DON’T GUESS...<strong>SOIL TEST</strong></p>
</section>

</body>
</html>
```